Tandem Hearth Works Pty Ltd

We need business cards for a company based in Perth, we install, service and maintain fire equipment.
On the front we want a great design with our logo and a small spot for our full company name, general company email address and office number. On the back we need space for our name, title, mobile number and email address on the back.

Target Market(s)

Facility managers and commercial/industrial building owners/occupiers.

Contact Information for Business Card

Font styles to use
Sans Serif

Requirements
Must have
• Please only submit 5 of your best samples.
Darker tones are preferred.
Nice to have
• We want to use, black, red and grey. Keep it modern and clean.
I've attached the company logo and a sample of a boarder we use on our emergency plans.
Should not have
• No preference. Let the designer choose.

```html
<!DOCTYPE html>
<html lang="en">
<head>
<meta charset="utf-8">
<title>Tandem Hearth Works – Business Card</title>
<link href="https://fonts.googleapis.com/css2?family=Roboto:wght@300;400;500;700;900&display=swap" rel="stylesheet">
<style>
  :root {
    --bg: #2a2a2c;
    --card-white: #ffffff;
    --card-dark: #1c1d1f;
    --card-dark-2: #232427;
    --red: #e5141f;
    --grey: #555659;
    --grey-light: #8a8b8e;
  }
  * { margin: 0; padding: 0; box-sizing: border-box; }
  html, body {
    width: 1200px; height: 1108px; overflow: hidden;
    background: var(--bg);
    font-family: "Roboto", Arial, sans-serif;
  }
  .canvas {
    position: relative; width: 1200px; height: 1108px;
    display: flex; justify-content: center; align-items: center; gap: 60px;
  }
  .card {
    width: 420px; height: 700px; border-radius: 26px;
    position: relative; overflow: hidden;
    box-shadow: 0 18px 40px rgba(0,0,0,.45);
  }
  .card-front { background: var(--card-white); text-align: center; }
  .brand-name {
    position: absolute; top: 120px; left: 0; right: 0;
    color: var(--red); font-weight: 900;
    font-size: 62px; line-height: 1; letter-spacing: 1px;
  }
  .brand-name span { display: block; }
  .person { position: absolute; top: 390px; left: 0; right: 0; }
  .person-name { color: var(--red); font-weight: 500; font-size: 30px; }
  .person-title { color: var(--grey); font-weight: 400; font-size: 22px; margin-top: 2px; }
  .icon-rule {
    position: absolute; top: 470px; left: 70px; right: 70px;
    display: flex; align-items: center; gap: 8px;
  }
  .icon-rule .rule { flex: 1; height: 1px; background: var(--grey-light); }
  .icon-rule svg { width: 24px; height: 24px; }
  .contact {
    position: absolute; top: 510px; left: 0; right: 0;
    color: var(--grey); font-size: 20px; line-height: 28px; font-weight: 400;
  }
  .contact .accent { color: var(--red); }
  .divider {
    position: absolute; top: 604px; left: 70px; right: 70px;
    height: 1px; background: var(--grey-light);
  }
  .address {
    position: absolute; top: 618px; left: 0; right: 0;
    color: var(--grey); font-size: 20px; line-height: 26px;
  }
  .card-back {
    background: var(--card-dark);
  }
  .back-texture {
    position: absolute; inset: 0;
    background: linear-gradient(160deg, var(--card-dark-2) 0%, var(--card-dark) 70%);
  }
  .back-brand {
    position: absolute; right: 56px; bottom: 118px;
    color: var(--red); font-weight: 900; font-size: 26px; line-height: 1.05;
    text-align: left;
  }
</style>
</head>
<body>
<main class="canvas">
  <section class="card card-front">
    <h1 class="brand-name"><span>TANDEM</span><span>HEARTH</span></h1>
    <div class="person">
      <p class="person-name">Liam Harcourt</p>
      <p class="person-title">Manager</p>
    </div>
    <div class="icon-rule">
      <span class="rule"></span>
      <svg viewBox="0 0 24 24" aria-label="phone" role="img"><circle cx="12" cy="12" r="12" fill="#e5141f"/><path d="M8 7c1 0 1.5 2 1.5 2.5S8.5 11 9 12s2 2.5 3 3 1.5-1 2-1 2.5.5 2.5 1.5-1 2-2 2C10 17.5 6.5 14 6.5 9.5c0-1.5.5-2.5 1.5-2.5z" fill="#fff"/></svg>
      <svg viewBox="0 0 24 24" aria-label="email" role="img"><circle cx="12" cy="12" r="12" fill="#e5141f"/><rect x="6" y="8" width="12" height="8" fill="none" stroke="#fff" stroke-width="1.5"/><path d="M6 8l6 5 6-5" fill="none" stroke="#fff" stroke-width="1.5"/></svg>
      <svg viewBox="0 0 24 24" aria-label="website" role="img"><circle cx="12" cy="12" r="12" fill="#e5141f"/><circle cx="12" cy="12" r="6" fill="none" stroke="#fff" stroke-width="1.5"/><path d="M6 12h12M12 6c-3 3-3 9 0 12M12 6c3 3 3 9 0 12" fill="none" stroke="#fff" stroke-width="1.2"/></svg>
      <span class="rule"></span>
    </div>
    <div class="contact">
      <p>08 6100 2451</p>
      <p>hello@tandemhearth.com</p>
      <p>www.<span class="accent">tandemhearth</span>.com</p>
    </div>
    <div class="divider"></div>
    <div class="address">
      <p>Your address, city</p>
      <p>state, ZIP 0000</p>
    </div>
  </section>

  <section class="card card-back">
    <div class="back-texture" role="img" aria-label="Faint tone-on-tone repeated company name texture"></div>
    <p class="back-brand">TANDEM<br>HEARTH</p>
  </section>
</main>
</body>
</html>
```